Redesign of LumoWordfind.com in Bootstrap 4

Current design of LumoWordfind.com is not responsive. We need to change it to latest version of Bootstrap 4 keeping essential elements in place.

Apart from home page, we need designs for http://www.lumowordfind.com/meaning/cat also.

Coding

Number of Pages Required

2 page

Colors
34a7d8

Requirements
Must have
• Bootstrap 4

```html
<!DOCTYPE html>
<html lang="en">
<head>
<meta charset="utf-8">
<title>Lumo Wordfind – Home</title>
<link rel="stylesheet" href="https://fonts.googleapis.com/css2?family=Roboto:wght@400;500&family=Open+Sans:ital@1&display=swap">
<style>
:root{
  --brand:#34a7d8;
  --brand-dark:#2a93c2;
  --orange:#f29a1d;
  --ink:#222;
  --muted:#555;
  --soft:#f5f5f5;
  --header:#efefef;
  --line:#e6e6e6;
  --white:#fff;
}
*{box-sizing:border-box;margin:0;padding:0}
html,body{width:927px;height:1200px;overflow:hidden}
body{position:relative;background:var(--white);font-family:"Roboto",Arial,sans-serif;color:var(--ink)}
.abs{position:absolute}
.bg-shapes{position:absolute;left:0;top:0}
.brand-name{left:58px;top:26px;font-size:22px;font-weight:500;color:var(--brand-dark);line-height:1}
.brand-name .dot{display:inline-block;width:12px;height:12px;background:var(--orange);margin-right:6px;vertical-align:middle}
.join{left:700px;top:20px;font-size:13px;font-weight:500;color:var(--orange)}
.login{left:798px;top:15px;width:71px;height:25px;background:var(--brand);border:1px solid var(--brand-dark);color:#fff;font-size:13px;text-align:center;line-height:23px;border-radius:2px}
.nav{left:57px;top:98px;display:flex;font-size:11px;color:#333}
.nav a{color:inherit;text-decoration:none;padding:0 9px 8px;margin-right:24px;border-bottom:3px solid transparent;height:22px}
.nav a.active{color:var(--brand);border-color:var(--brand)}
.nav-line{left:0;top:120px;width:927px;height:1px;background:var(--line)}
.hero-title{left:0;width:927px;top:148px;text-align:center;font-size:22px;color:var(--brand-dark)}
.search{left:245px;top:193px;width:438px;height:44px;background:#2b2b2b;border-radius:2px}
.search-field{left:9px;top:7px;width:314px;height:29px;background:#fff;font:italic 10px "Open Sans",sans-serif;color:#999;padding:8px 15px}
.search-btn{left:336px;top:0;width:102px;height:44px;border-left:1px solid #111;color:#fff;font-size:13px;display:flex;align-items:center;justify-content:center;gap:7px}
.hero-text{left:0;width:927px;top:275px;text-align:center;font:italic 12px/17px "Open Sans",sans-serif;color:#fff}
.learn{left:405px;top:327px;width:117px;height:32px;background:#fff;color:#222;font-size:12px;text-align:center;line-height:32px;border-radius:2px}
.books{left:54px;top:468px;width:126px;height:124px;background:linear-gradient(160deg,#6a9a3a,#8a5a30 55%,#3a5a7a);border-radius:6px}
.features h2{position:absolute;left:195px;top:461px;font-size:18px;font-weight:400;color:var(--brand-dark)}
.features ul{position:absolute;left:196px;top:497px;list-style:none;font-size:12px;color:var(--muted)}
.features li{height:25.6px;display:flex;align-items:center;gap:8px}
.features li span.free{color:var(--brand)}
.wotd{left:614px;top:470px;width:256px;height:136px;background:#f3f3f3}
.wotd-head{height:35px;background:var(--brand);color:#fff;font-size:13px;padding:11px 14px;letter-spacing:.3px}
.wotd-word{text-align:center;font-size:17px;margin-top:16px}
.wotd-phon{text-align:center;font-size:10px;color:#444;letter-spacing:2px;margin-top:3px}
.wotd-foot{position:absolute;left:0;top:103px;width:256px;border-top:1px solid #e2e2e2;height:33px}
.show-def{position:absolute;right:14px;top:6px;background:#2b2b2b;color:#fff;font-size:10px;padding:5px 10px;border-radius:2px}
.card{width:190px;text-align:center}
.card h3{font-size:14px;font-weight:500;margin-top:10px}
.card p{font-size:10px;line-height:14.5px;color:var(--muted);margin-top:9px;height:37px}
.card .more{font-size:11px;margin-top:7px}
.browse{left:374px;top:931px;width:181px;height:34px;border:2px solid var(--brand);border-radius:3px;text-align:center;line-height:30px;color:var(--brand-dark);font-size:14px;letter-spacing:.5px}
.foot-col{color:#fff}
.foot-col h4{font-size:13px;font-weight:400;letter-spacing:.4px;margin-bottom:9px}
.foot-col a{display:block;color:#fff;text-decoration:none;font-size:11px;line-height:17.5px}
.foot-brand{left:760px;top:1030px;width:108px;text-align:right;color:#fff;font-size:20px;font-weight:500}
.foot-tag{left:660px;top:1096px;width:208px;text-align:right;font:italic 9.5px/13px "Open Sans",sans-serif;color:#cfeaf7}
.foot-rule{left:0;top:1139px;width:927px;height:1px;background:rgba(255,255,255,.25)}
.foot-bottom{left:0;width:927px;text-align:center;color:#fff}
</style>
</head>
<body>
<svg class="bg-shapes" width="927" height="1200" aria-hidden="true">
  <polygon points="0,0 927,0 927,54 0,85" fill="#efefef"/>
  <polygon points="0,228 927,198 927,416 0,416" fill="#34a7d8"/>
  <ellipse cx="480" cy="330" rx="260" ry="70" fill="#ffffff" opacity=".08"/>
  <polygon points="0,674 927,644 927,904 0,904" fill="#f5f5f5"/>
  <polygon points="0,1008 927,978 927,1200 0,1200" fill="#34a7d8"/>
</svg>

<header>
  <div class="abs brand-name"><span class="dot"></span>Lumo<br><span style="font-size:12px;padding-left:18px">WORDFIND</span></div>
  <div class="abs join">Join for FREE!</div>
  <div class="abs login">LogIn</div>
  <nav class="abs nav">
    <a class="active" href="#">HOME</a><a href="#">IDIOMS</a><a href="#">COMMON ERRORS</a><a href="#">CROSSWORD</a><a href="#">BLOG</a><a href="#">CONTACT</a>
  </nav>
  <div class="abs nav-line"></div>
</header>

<section class="hero">
  <h1 class="abs hero-title" style="font-weight:400">LUMO ENGLISH DICTIONARY</h1>
  <div class="abs search">
    <div class="abs search-field">Search our knowledge base...</div>
    <div class="abs search-btn">
      <svg width="12" height="12" viewBox="0 0 12 12"><circle cx="5" cy="5" r="3.8" fill="none" stroke="#fff" stroke-width="1.8"/><line x1="7.8" y1="7.8" x2="11" y2="11" stroke="#fff" stroke-width="2"/></svg>Search
    </div>
  </div>
  <p class="abs hero-text">At vero eos et accusamus et iusto odio dignissimos ducimus qui blanditiis praesentium voluptatum deleniti atque<br>corrupti quos dolores et quas molestias excepturi sint occaecati cupiditate non provident</p>
  <div class="abs learn">LEARN MORE</div>
</section>

<section class="features">
  <div class="abs books" role="img" aria-label="Stack of books illustration"></div>
  <h2>SEARCH, SAVE AND MASTER WORDS</h2>
  <ul>
    <li><svg width="14" height="14" viewBox="0 0 14 14"><circle cx="7" cy="7" r="6" fill="none" stroke="#34a7d8" stroke-width="1.5"/><path d="M4 7h5M7 4.5 9.5 7 7 9.5" fill="none" stroke="#34a7d8" stroke-width="1.5"/></svg>Search from more than 300,000 words and phrases</li>
    <li><svg width="14" height="14" viewBox="0 0 14 14"><circle cx="7" cy="7" r="6" fill="none" stroke="#34a7d8" stroke-width="1.5"/><path d="M4 7h5M7 4.5 9.5 7 7 9.5" fill="none" stroke="#34a7d8" stroke-width="1.5"/></svg>Multiple usages to clarify the context</li>
    <li><svg width="14" height="14" viewBox="0 0 14 14"><circle cx="7" cy="7" r="6" fill="none" stroke="#34a7d8" stroke-width="1.5"/><path d="M4 7h5M7 4.5 9.5 7 7 9.5" fill="none" stroke="#34a7d8" stroke-width="1.5"/></svg>Audio, phonetics, meanings, synonyms and antonyms</li>
    <li><svg width="14" height="14" viewBox="0 0 14 14"><circle cx="7" cy="7" r="6" fill="none" stroke="#34a7d8" stroke-width="1.5"/><path d="M4 7h5M7 4.5 9.5 7 7 9.5" fill="none" stroke="#34a7d8" stroke-width="1.5"/></svg>Save the words to your personal deck and access from anywhere</li>
    <li><svg width="14" height="14" viewBox="0 0 14 14"><circle cx="7" cy="7" r="6" fill="none" stroke="#34a7d8" stroke-width="1.5"/><path d="M4 7h5M7 4.5 9.5 7 7 9.5" fill="none" stroke="#34a7d8" stroke-width="1.5"/></svg>It's <span class="free">FREE</span></li>
  </ul>
  <aside class="abs wotd">
    <div class="wotd-head">WORD OF THE DAY</div>
    <div class="wotd-word">ascendancy <svg width="10" height="12" viewBox="0 0 10 12" style="margin-left:8px"><path d="M1 4h3l4-3v10L4 8H1z" fill="#34a7d8"/></svg></div>
    <div class="wotd-phon">/ sndnsi /</div>
    <div class="wotd-foot">
      <svg class="abs" style="left:12px;top:10px" width="40" height="15" viewBox="0 0 40 15"><circle cx="3" cy="12" r="2" fill="#34a7d8"/><path d="M1 6a8 8 0 0 1 8 8M1 1a13 13 0 0 1 13 13" fill="none" stroke="#34a7d8" stroke-width="2"/><circle cx="30" cy="7.5" r="6.5" fill="#34a7d8"/></svg>
      <span class="show-def">Show Definition</span>
    </div>
  </aside>
</section>

<section class="tools">
  <div class="abs card" style="left:56px;top:702px">
    <svg width="68" height="68" viewBox="0 0 68 68"><circle cx="34" cy="34" r="32.5" fill="none" stroke="#34a7d8" stroke-width="2"/><rect x="30" y="18" width="22" height="15" rx="2" fill="none" stroke="#34a7d8" stroke-width="2"/><circle cx="26" cy="36" r="5" fill="#34a7d8"/><path d="M16 50a10 8 0 0 1 20 0z" fill="#34a7d8"/></svg>
    <h3>English Tidbit</h3>
    <p>To "gibe" is to taunt. Gibe is however slowly going out of use. Jibe means to agree but is often used.</p>
    <div class="more">READ MORE</div>
  </div>
  <div class="abs card" style="left:265px;top:702px">
    <svg width="68" height="68" viewBox="0 0 68 68"><circle cx="34" cy="34" r="32.5" fill="none" stroke="#34a7d8" stroke-width="2"/><path d="M22 26h7a4 4 0 1 1 8 0h7v8a4 4 0 1 1 0 8v6H22v-7a4 4 0 1 0 0-8z" fill="#34a7d8"/></svg>
    <h3>Daily Crossword</h3>
    <p>Crossword Lovers!<br>Take this daily crossword challenge from Lumo Wordfind.</p>
    <div class="more">READ MORE</div>
  </div>
  <div class="abs card" style="left:473px;top:702px">
    <svg width="68" height="68" viewBox="0 0 68 68"><circle cx="34" cy="34" r="32.5" fill="none" stroke="#34a7d8" stroke-width="2"/><circle cx="34" cy="34" r="16" fill="#34a7d8"/></svg>
    <h3>Emberfox Addon</h3>
    <p>Add this tool to your Emberfox and quickly look up for definitions from any website without leaving the page.</p>
    <div class="more">READ MORE</div>
  </div>
  <div class="abs card" style="left:682px;top:702px">
    <svg width="68" height="68" viewBox="0 0 68 68"><circle cx="34" cy="34" r="32.5" fill="none" stroke="#34a7d8" stroke-width="2"/><rect x="25" y="20" width="18" height="28" rx="3" fill="none" stroke="#34a7d8" stroke-width="2.5"/><circle cx="34" cy="44" r="1.5" fill="#34a7d8"/></svg>
    <h3>Designed for Ophone</h3>
    <p>Lumo Wordfind is specially designed for your Ophone to quickly lookup meaning, usages and audio of words.</p>
    <div class="more">READ MORE</div>
  </div>
</section>

<div class="abs browse">BROWSE DICTIONARY</div>

<footer>
  <div class="abs foot-col" style="left:57px;top:1033px"><h4>LUMOWORDFIND.COM</h4><a href="#">FAQ</a><a href="#">Contact</a><a href="#">Blog</a></div>
  <div class="abs foot-col" style="left:273px;top:1033px"><h4>LEGAL</h4><a href="#">Privacy Policy</a><a href="#">Terms of Use</a></div>
  <div class="abs foot-col" style="left:475px;top:1033px"><h4>OTHERS</h4><a href="#">Popular Words</a><a href="#">Common Errors in English</a><a href="#">Equivalency Prep Online</a></div>
  <div class="abs foot-brand">Lumo<br><span style="font-size:12px">WORDFIND</span></div>
  <p class="abs foot-tag">At vero eos et accusamus et iusto odio<br>dignissimos ducimus qui blanditiis</p>
  <div class="abs foot-rule"></div>
  <p class="abs foot-bottom" style="top:1155px;font-size:12px">Lumo Wordfind Dictionary: Meaning/Definition, Audio, Phonetics, Usages and more</p>
  <p class="abs foot-bottom" style="top:1175px;font-size:10px">Copyright © 2016, All rights reserved.</p>
</footer>
</body>
</html>
```